Custom Manufacturing Company square space website design

I own a custom manufacturing company that uses precision cutting technology to manufacture project components over a couple industries. We have an industrial CNC router and state of the art edge bander and cut a lot of cabinetry components for cabinet shops, builders, closet companies, ect. We offer design and assembly for any cabinetry or can build cabinets to spec. We also cut components for other industries out of wood, plastics, acryclics, ect. We offer design engineering services, product development protype services. we have a 3D printer farm. We want our communicate trust, dependability, and the value we place on client relationships.

We essentially want a credibility website. Landing page and drops downs for services we offer, capabilites, about us, contact

```html
<!DOCTYPE html>
<html lang="en">
<head>
<meta charset="utf-8">
<title>Northline CNC – Custom Manufacturing</title>
<link href="https://fonts.googleapis.com/css2?family=Poppins:wght@300;400;500;600;700&family=Syncopate:wght@400;700&display=swap" rel="stylesheet">
<style>
:root{
  --green:#739c77;
  --green-dark:#5f8a64;
  --green-soft:#86ab89;
  --ink:#1d1d1d;
  --text:#555;
  --muted:#777;
  --gray-bg:#f2f2f2;
  --field:#f3f3f3;
  --footer:#1e1e1e;
  --white:#fff;
}
*{margin:0;padding:0;box-sizing:border-box}
html,body{width:1200px;height:3322px;overflow:hidden}
body{position:relative;font-family:'Poppins',sans-serif;color:var(--ink);background:var(--white)}
.abs{position:absolute}
.display{font-family:'Syncopate',sans-serif;font-weight:700;letter-spacing:6px}
.photo{position:absolute}

/* header */
.site-header{position:absolute;left:0;top:0;width:1200px;height:89px;background:var(--white)}
.brand{position:absolute;left:143px;top:28px;display:flex;align-items:center;gap:8px;font-weight:600;font-size:15px;letter-spacing:2px;color:var(--ink)}
.brand-square{width:16px;height:16px;border:2px solid var(--ink)}
.main-nav{position:absolute;top:33px;font-size:14.5px;color:var(--ink)}
.main-nav span{position:absolute;white-space:nowrap}
.main-nav .active{border-bottom:1.5px solid var(--ink);padding-bottom:2px}
.btn{display:flex;align-items:center;justify-content:center;font-weight:600;text-transform:uppercase;letter-spacing:.5px}
.btn-quote{position:absolute;left:871px;top:23px;width:183px;height:45px;background:var(--green);color:var(--white);font-size:14px}

/* hero */
.hero-text{position:absolute;left:599px;color:var(--white)}
.btn-start{position:absolute;left:599px;top:258px;width:136px;height:39px;background:var(--white);color:var(--green);font-size:13.5px}
.frame-line{position:absolute;border:3px solid var(--green)}

/* about */
.eyebrow{position:absolute;left:143px;top:784px;color:var(--green);font-weight:600;font-size:15.5px;letter-spacing:.5px;display:flex;align-items:center;gap:10px}
.eyebrow::after{content:"";width:42px;height:1.5px;background:var(--green)}
.section-title{font-family:'Syncopate',sans-serif;font-weight:700;font-size:29px;letter-spacing:7px}
.about-copy{position:absolute;left:143px;top:859px;width:434px;font-size:14px;line-height:22px;color:var(--text);text-align:justify}
.about-copy p+p{margin-top:10px}
.btn-learn{position:absolute;left:143px;top:1018px;width:132px;height:41px;background:var(--green);color:var(--white);font-size:13px}

/* services */
.services{position:absolute;left:0;top:1148px;width:1200px;height:734px;background:var(--gray-bg)}
.ruled-title{position:absolute;left:0;width:1200px;display:flex;justify-content:center;align-items:center;gap:14px}
.ruled-title::before,.ruled-title::after{content:"";width:44px;height:1.5px;background:currentColor;opacity:.6}
.service-card{position:absolute;width:304px;height:251px;background:var(--white);text-align:center}
.service-card svg{margin-top:28px}
.service-card h3{font-weight:500;font-size:16px;margin-top:12px;letter-spacing:.3px}
.service-card p{font-size:13px;line-height:22px;color:var(--muted);margin:12px auto 0;width:210px}
.service-card a{display:inline-block;margin-top:14px;font-size:12.5px;color:var(--green);text-decoration:underline;text-underline-offset:3px}

/* capabilities */
.capabilities{position:absolute;left:0;top:1882px;width:1200px;height:389px;background:linear-gradient(90deg,var(--green) 0%,var(--green-soft) 55%,var(--green) 100%)}
.cap-card{position:absolute;color:var(--white)}
.cap-card h4{position:absolute;left:73px;top:256px;font-weight:700;font-size:24px;white-space:nowrap}
.cap-card p{position:absolute;left:73px;top:300px;width:360px;font-size:14px;line-height:24px}

/* form */
.quote-card{position:absolute;left:200px;top:2546px;width:800px;height:348px;background:var(--white);box-shadow:0 0 18px rgba(0,0,0,.07)}
.field{position:absolute;background:var(--field);border:1px solid #e6e6e6;font-size:11.5px;color:#666;padding:14px 17px 0}
.btn-submit{position:absolute;left:503px;top:2806px;width:171px;height:43px;background:var(--green);color:var(--white);font-size:13.5px}

/* footer */
.site-footer{position:absolute;left:0;top:2974px;width:1200px;height:348px;background:var(--footer);color:var(--white)}
.footer-head{position:absolute;top:60px;font-weight:700;font-size:15px;letter-spacing:.3px}
.footer-list{position:absolute;font-size:13px;line-height:24px}
.contact-item{position:absolute;left:389px;font-size:13.5px;line-height:20px}
.contact-item b{font-size:11.5px;font-weight:600;display:block}
.contact-item svg{position:absolute;left:-24px;top:2px}
</style>
</head>
<body>

<header class="site-header">
  <div class="brand"><span class="brand-square"></span>NORTHLINE CNC</div>
  <nav class="main-nav">
    <span class="active" style="left:312px">Home</span>
    <span style="left:382px">Services We Offer</span>
    <span style="left:535px">Capabilities</span>
    <span style="left:648px">About Us</span>
    <span style="left:739px">Contact</span>
    <svg style="position:absolute;left:828px;top:4px" width="14" height="14" viewBox="0 0 14 14"><circle cx="6" cy="6" r="4.5" fill="none" stroke="#1d1d1d" stroke-width="2"/><line x1="9.5" y1="9.5" x2="13" y2="13" stroke="#1d1d1d" stroke-width="2"/></svg>
  </nav>
  <div class="btn btn-quote">Free Instant Quote</div>
</header>

<section class="hero">
  <div class="photo" role="img" aria-label="Timber roof framing under construction" style="left:0;top:89px;width:480px;height:282px;background:linear-gradient(135deg,#c99a6e,#e3c3a0 50%,#8d6a4b)"></div>
  <div class="photo" role="img" aria-label="Factory floor with machinery under a green overlay" style="left:480px;top:89px;width:720px;height:282px;background:linear-gradient(90deg,#7ea582,#8db291 60%,#7ba07f)"></div>
  <div class="hero-text" style="top:146px;font-size:17px;font-weight:500">Welcome To</div>
  <div class="hero-text display" style="top:180px;font-size:29px;letter-spacing:8px;font-weight:400">NORTHLINE CNC</div>
  <div class="hero-text" style="top:225px;font-size:14.5px">Custom Manufacturing Solutions for the building industry.</div>
  <div class="btn btn-start">Get Started</div>
  <div class="photo" role="img" aria-label="Large-scale 3D printer extruding a concrete wall outdoors" style="left:0;top:371px;width:719px;height:300px;background:linear-gradient(160deg,#6f8c5e,#9aa3a6 45%,#5c6670)"></div>
  <div class="photo" role="img" aria-label="Close-up of a 3D printer nozzle in blue light" style="left:719px;top:371px;width:481px;height:300px;background:linear-gradient(135deg,#1f3f55,#5f86a0 55%,#2b4a60)"></div>
  <div class="frame-line" style="left:140px;top:668px;width:920px;height:28px;border-top:none"></div>
</section>

<section class="about">
  <div class="eyebrow">ABOUT US</div>
  <div class="abs section-title" style="left:143px;top:808px">NORTHLINE CNC</div>
  <div class="about-copy">
    <p>Lorem ipsum dolor sit amet, consectetur adipiscing elit, sed do eiusmod tempor incididunt ut labore et dolore magna aliqua. Ut enim ad minim veniam, quis nostrud exercitation ullamco laboris aliquipcommodo consequat.</p>
    <p>Duis aute irure dolor in reprehenderit in voluptate velit esse cillum dolore eu fugiat nulla pariatur.</p>
  </div>
  <div class="btn btn-learn">Learn More</div>
  <div class="abs" style="left:663px;top:777px;width:377px;height:292px;background:var(--green)"></div>
  <div class="photo" role="img" aria-label="Two engineers reviewing a laptop on a factory floor" style="left:647px;top:785px;width:407px;height:276px;background:linear-gradient(135deg,#3e5a78,#8aa0b6 50%,#2f4760)"></div>
</section>

<section class="services">
  <div class="ruled-title" style="top:62px;color:var(--ink)"><span class="section-title" style="font-size:27px;letter-spacing:8px">SERVICES WE OFFER</span></div>

  <div class="photo" role="img" aria-label="Hand sketching beside an architectural model" style="left:143px;top:155px;width:304px;height:251px;background:linear-gradient(135deg,#3a4a5a,#c8a27c 55%,#e6d4bd)"></div>
  <div class="service-card" style="left:447px;top:155px">
    <svg width="46" height="46" viewBox="0 0 46 46" fill="none" stroke="#739c77" stroke-width="2.5"><path d="M23 12l10 5v12l-10 5-10-5V17z"/><path d="M13 17l10 5 10-5M23 22v12"/><path d="M7 23a16 16 0 0 1 16-16M39 23a16 16 0 0 1-16 16"/></svg>
    <h3>PRODUCT DEVELOPMENT</h3>
    <p>Lorem ipsum amconsectetur adipiscingelit,sed do eiusmod tempor amconsector.</p>
    <a>READ MORE</a>
  </div>
  <div class="photo" role="img" aria-label="Technician operating a precision machine" style="left:752px;top:155px;width:304px;height:251px;background:linear-gradient(135deg,#2d3f52,#6f8aa0 50%,#c5ced6)"></div>

  <div class="service-card" style="left:143px;top:406px">
    <svg width="46" height="46" viewBox="0 0 46 46" fill="none" stroke="#739c77" stroke-width="2.5"><rect x="9" y="7" width="30" height="32"/><circle cx="24" cy="23" r="6"/><path d="M5 11v24M43 11v24"/></svg>
    <h3>DESIGN ENGINEERING</h3>
    <p>Lorem ipsum amconsectetur adipiscingelit,sed do eiusmod tempor amconsector.</p>
    <a>READ MORE</a>
  </div>
  <div class="photo" role="img" aria-label="Robotic arm assembling circuit boards" style="left:447px;top:406px;width:305px;height:251px;background:linear-gradient(135deg,#5d6d7a,#a9b4bc 50%,#3e5a4a)"></div>
  <div class="service-card" style="left:752px;top:406px">
    <svg width="46" height="46" viewBox="0 0 46 46" fill="none" stroke="#739c77" stroke-width="2.5"><rect x="6" y="6" width="34" height="34"/><path d="M6 16h34M16 26h14M23 16v10M14 34h18"/></svg>
    <h3>3D PRINTER FARM</h3>
    <p>Lorem ipsum amconsectetur adipiscingelit,sed do eiusmod tempor amconsector.</p>
    <a>READ MORE</a>
  </div>
</section>

<section class="capabilities">
  <div class="ruled-title" style="top:40px;color:var(--white)"><span class="section-title" style="font-size:27px;letter-spacing:8px">CAPABILITIES</span></div>
  <div class="abs" style="left:170px;top:106px;width:860px;text-align:center;color:var(--white);font-size:17px;line-height:23px">Sed ut perspiciatis unde omnis iste natus error sit voluptatem accusantium doloremque laudantium, totam rem aperiam, eaque ipsa quae ab illo inventore veritatis.</div>
</section>

<div class="cap-card" style="left:143px;top:2083px;width:566px;height:378px">
  <div class="photo" role="img" aria-label="Worker installing composite decking boards" style="left:0;top:0;width:566px;height:378px;background:linear-gradient(180deg,#b9c2cb,#6b625a 55%,#3e3833)"></div>
  <h4>LOREM IPSUM DOLOR</h4>
  <p>Lorem ipsum dolor sit amet, consectetur adipiscing elit, sed do eiusmod tempor incididunt.</p>
  <svg style="position:absolute;left:484px;top:316px" width="18" height="18" viewBox="0 0 18 18"><circle cx="9" cy="9" r="8" fill="#fff"/><path d="M5 9h7M9 5.5L12.5 9 9 12.5" stroke="#333" stroke-width="1.8" fill="none"/></svg>
</div>
<div class="cap-card" style="left:722px;top:2083px;width:478px;height:378px">
  <div class="photo" role="img" aria-label="Wooden deck with outdoor benches" style="left:0;top:0;width:478px;height:378px;background:linear-gradient(160deg,#4f6e3e,#6b5a49 45%,#3a332d)"></div>
  <h4 style="left:73px">LOREM IPSUM DOLOR</h4>
  <p style="left:73px">Lorem ipsum dolor sit amet, consectetur adipiscing elit, sed do eiusmod tempor incididunt.</p>
</div>

<section class="quote-card">
  <svg class="abs" style="left:33px;top:58px" width="48" height="52" viewBox="0 0 48 52" fill="none" stroke="#739c77" stroke-width="2"><path d="M8 2h24l10 10v38H8z"/><path d="M32 2v10h10M15 14h12M15 20h18"/><rect x="2" y="27" width="42" height="15" rx="2"/><text x="23" y="39" font-family="Poppins,sans-serif" font-size="11" fill="#739c77" stroke="none" text-anchor="middle">MSG</text></svg>
  <div class="abs" style="left:33px;top:124px;font-size:14.5px">Get In Touch</div>
  <div class="abs" style="left:33px;top:150px;font-size:25px;font-weight:700">Request a quote</div>
  <div class="abs" style="left:34px;top:194px;width:250px;font-size:12px;line-height:20px;color:var(--muted)">Lorem ipsum dolor sit amet, consectetur adipiscing elit, sed do eiusmod</div>
  <svg class="abs" style="left:33px;top:258px" width="40" height="30" viewBox="0 0 40 30" fill="none" stroke="#9bbd9e" stroke-width="2"><path d="M8 6c-3 3-3 9 4 16s13 7 16 4l-5-5-3 2c-2-1-5-4-6-6l2-3z"/></svg>
  <div class="abs" style="left:80px;top:258px;font-size:14.5px;color:var(--green)">Call Us Today !</div>
  <div class="abs" style="left:80px;top:280px;font-size:14.5px;font-weight:700;letter-spacing:.5px">+1-555-014-2290</div>
  <div class="abs" style="left:63px;top:346px;width:699px;height:3px;background:var(--green)"></div>
</section>
<div class="field" style="left:501px;top:2591px;width:218px;height:35px;padding-top:10px">Name</div>
<div class="field" style="left:749px;top:2591px;width:218px;height:35px;padding-top:10px">Last Name</div>
<div class="field" style="left:501px;top:2650px;width:218px;height:35px;padding-top:10px">Phone Number</div>
<div class="field" style="left:749px;top:2650px;width:218px;height:35px;padding-top:10px">Email Address</div>
<div class="field" style="left:501px;top:2708px;width:466px;height:76px">Additional Details...</div>
<div class="btn btn-submit">Submit Request</div>
<svg class="abs" style="left:701px;top:2818px" width="18" height="18" viewBox="0 0 18 18" fill="none" stroke="#739c77" stroke-width="1.5"><circle cx="9" cy="9" r="8"/><circle cx="9" cy="9" r="3"/></svg>
<div class="abs" style="left:731px;top:2818px;font-size:13px;color:#444;letter-spacing:.3px">I accept The Privacy and Terms</div>

<div class="frame-line" style="left:140px;top:2961px;width:920px;height:20px;border-bottom:none;z-index:2"></div>

<footer class="site-footer">
  <div class="abs" style="left:143px;top:128px;display:flex;align-items:center;gap:8px;font-weight:600;font-size:17px;letter-spacing:2.5px"><span style="width:16px;height:16px;border:2px solid #fff"></span>NORTHLINE CNC</div>
  <div class="abs" style="left:183px;top:189px;display:flex;gap:14px">
    <span style="width:12px;height:12px;border-radius:50%;background:#fff"></span>
    <span style="width:12px;height:12px;border-radius:50%;background:#fff"></span>
    <span style="width:12px;height:12px;border-radius:50%;background:#fff"></span>
    <span style="width:12px;height:12px;border-radius:50%;background:#fff"></span>
  </div>

  <div class="footer-head" style="left:389px">OUR OFFICE ADDRESS</div>
  <div class="contact-item" style="top:97px">
    <svg width="12" height="12" viewBox="0 0 12 12"><path d="M2 1c-2 2 0 6 3 8s5 3 6 1l-2-2-1.5 1C6 8 4.5 6.5 4 5l1-1.5z" fill="#739c77"/></svg>
    <b>Phone</b>555-014-2290</div>
  <div class="contact-item" style="top:145px">
    <svg width="12" height="10" viewBox="0 0 12 10"><rect width="12" height="10" fill="#739c77"/><path d="M0 0l6 5 6-5" stroke="#1e1e1e" fill="none"/></svg>
    <b>Email</b>hello@northlinecnc.example</div>
  <div class="contact-item" style="top:194px;width:190px">
    <svg width="10" height="14" viewBox="0 0 10 14"><path d="M5 0a5 5 0 0 1 5 5c0 4-5 9-5 9S0 9 0 5a5 5 0 0 1 5-5z" fill="#739c77"/><circle cx="5" cy="5" r="2" fill="#1e1e1e"/></svg>
    <b>Location</b>27 Millwright Ave, Cedar Falls, MN 55000</div>

  <div class="footer-head" style="left:648px">COMPANY</div>
  <div class="footer-list" style="left:657px;top:88px">Home<br>Services We Offer<br>Capabilities<br>About Us<br>Contact</div>

  <div class="footer-head" style="left:831px">STIL HAVE QUESTIOS?</div>
  <div class="abs" style="left:832px;top:93px;width:240px;font-size:12px;line-height:18px">Lorem ipsum dolor sit amet, consectetur adipiscing elit, sed do eiusmod tempor incididunt ut labore.</div>
  <div class="btn abs" style="left:833px;top:174px;width:185px;height:38px;background:var(--green);font-size:13.5px">Get In Touch</div>

  <div class="abs" style="left:143px;top:265px;width:913px;height:1px;background:#3e3e3e"></div>
  <div class="abs" style="left:982px;top:258px;width:74px;height:17px;border-radius:9px;background:var(--green);font-size:11px;text-align:center;line-height:17px">&#8593; Go Up</div>
  <div class="abs" style="left:143px;top:300px;font-size:13px">© 2023 Northline CNC | All Rights Reserved</div>
  <div class="abs" style="left:722px;top:300px;font-size:13px;word-spacing:2px">Privacy Policy &nbsp;|&nbsp; Cookie Policy &nbsp;|&nbsp; Terms Of Services</div>
</footer>

</body>
</html>
```